Need a book cover design for book titled: Crossing the Quiet River--Simple Practices for Daily Calm

This book describes and presents tools to connect with and activate the Lightbody that we all carry within us. It talks about the Lighbody, brief history, lightbody levels and offers exercises to bring light into the body.
I envision a design that shows a physical body changing into light /surrounded by light; a resurrected body ascending to higher dimensions of Spirit o anything comparable .

Need extra days to review

Need extra days to review

Mature audience of spiritual seekers and those on spiritual path

• Space on backcover for book summary at top and title and author name on spine.

```html
<!DOCTYPE html>
<html lang="en">
<head>
<meta charset="utf-8">
<title>Crossing the Quiet River — Cover Spread</title>
<link rel="stylesheet" href="https://fonts.googleapis.com/css2?family=Cinzel:wght@400&family=Josefin+Sans:wght@700&family=Barlow:ital,wght@0,500;0,700;1,600&display=swap">
<style>
  :root {
    --backdrop: #e3e3e3;
    --space-deep: #1c1124;
    --space-violet: #2c1a35;
    --nebula-teal: #2f8fa0;
    --nebula-cyan: #7fe3f0;
    --nebula-amber: #c7792f;
    --glow-white: #f4f8ff;
    --ink-light: #ffffff;
    --ink-soft: #e9e6ee;
  }
  * { margin: 0; padding: 0; box-sizing: border-box; }
  html, body { width: 1200px; height: 800px; overflow: hidden; }
  body {
    background: var(--backdrop);
    display: flex;
    align-items: center;
    justify-content: center;
  }
  .cover-spread {
    display: flex;
    width: 740px;
    height: 540px;
    box-shadow: 0 18px 40px rgba(0,0,0,0.25);
  }
  .panel {
    position: relative;
    height: 100%;
    overflow: hidden;
    background: var(--space-deep);
  }
  .panel-back { width: 340px; }
  .panel-spine { width: 60px; }
  .panel-front { width: 340px; }

  .space-art {
    position: absolute;
    inset: 0;
    width: 100%;
    height: 100%;
  }

  .title-rule {
    height: 1px;
    background: var(--ink-light);
  }
  .book-title {
    font-family: "Cinzel", serif;
    font-weight: 400;
    color: var(--ink-light);
    line-height: 1;
    white-space: nowrap;
  }
  .book-subtitle {
    font-family: "Josefin Sans", sans-serif;
    font-weight: 700;
    color: var(--ink-light);
    text-transform: uppercase;
    white-space: nowrap;
  }

  /* Back cover */
  .back-heading {
    position: absolute;
    left: 20px;
    right: 20px;
    top: 52px;
  }
  .back-heading .book-title { font-size: 22px; margin-top: 8px; }
  .back-heading .book-subtitle { font-size: 9.5px; letter-spacing: 0.28em; margin-top: 8px; }
  .back-summary {
    position: absolute;
    left: 34px;
    right: 22px;
    top: 170px;
    font-family: "Barlow", sans-serif;
    font-weight: 500;
    font-size: 9.5px;
    line-height: 1.4;
    color: var(--ink-soft);
  }
  .back-summary p + p { margin-top: 12px; }
  .back-author {
    position: absolute;
    left: 36px;
    bottom: 50px;
    font-family: "Barlow", sans-serif;
    font-weight: 700;
    font-size: 26px;
    line-height: 1;
    color: var(--ink-light);
  }

  /* Spine */
  .spine-text {
    position: absolute;
    top: 0;
    left: 50%;
    width: 540px;
    height: 60px;
    transform-origin: 0 0;
    transform: rotate(90deg) translate(0, -30px);
    display: flex;
    align-items: center;
    padding: 0 22px 0 30px;
  }
  .spine-titles { display: flex; flex-direction: column; gap: 4px; }
  .spine-text .book-title { font-size: 21px; }
  .spine-text .book-subtitle { font-size: 8px; letter-spacing: 0.32em; }
  .spine-author {
    margin-left: auto;
    font-family: "Barlow", sans-serif;
    font-weight: 600;
    font-style: italic;
    font-size: 11px;
    color: var(--ink-light);
  }

  /* Front cover */
  .front-heading {
    position: absolute;
    left: 18px;
    right: 18px;
    bottom: 46px;
  }
  .front-heading .book-title { font-size: 22px; margin-top: 8px; }
  .front-heading .book-subtitle { font-size: 9.5px; letter-spacing: 0.26em; margin-top: 6px; }
  .front-author {
    margin-top: 14px;
    text-align: center;
    font-family: "Barlow", sans-serif;
    font-weight: 600;
    font-style: italic;
    font-size: 11px;
    color: var(--ink-light);
  }
  .front-author .dot { font-style: normal; margin: 0 6px; }
</style>
</head>
<body>
  <main class="cover-spread">
    <section class="panel panel-back">
      <svg class="space-art" viewBox="0 0 340 540" preserveAspectRatio="none" role="img" aria-label="Deep space nebula with a faint blue planet and scattered stars">
        <defs>
          <radialGradient id="backNebula" cx="0.75" cy="0.55" r="0.75">
            <stop offset="0" stop-color="var(--nebula-teal)" stop-opacity="0.6"/>
            <stop offset="0.45" stop-color="var(--space-violet)"/>
            <stop offset="1" stop-color="var(--space-deep)"/>
          </radialGradient>
        </defs>
        <rect width="340" height="540" fill="url(#backNebula)"/>
      </svg>
      <header class="back-heading">
        <div class="title-rule"></div>
        <h2 class="book-title">Crossing the Quiet River</h2>
        <p class="book-subtitle">Simple Practices for Daily Calm</p>
      </header>
      <div class="back-summary">
        <p>This gentle guide invites you to slow down, breathe deeply and notice the stillness that waits beneath the noise of every busy day, ready whenever you return to it.</p>
        <p>Through short exercises, quiet reflections and simple rituals, you will learn to meet tension with patience, rest your mind between tasks and carry a sense of calm from morning until night. Each chapter offers one small practice that fits easily into ordinary life.</p>
        <p>Written for seekers at every stage of the path, this book is a companion for the moments when you need to pause, listen and find your footing again on the far bank of the river.</p>
      </div>
      <p class="back-author">Author<br>Name</p>
    </section>

    <section class="panel panel-spine">
      <svg class="space-art" viewBox="0 0 60 540" preserveAspectRatio="none" role="img" aria-label="Dark violet starfield">
        <defs>
          <linearGradient id="spineSpace" x1="0" y1="0" x2="0" y2="1">
            <stop offset="0" stop-color="var(--space-violet)"/>
            <stop offset="1" stop-color="var(--space-deep)"/>
          </linearGradient>
        </defs>
        <rect width="60" height="540" fill="url(#spineSpace)"/>
      </svg>
      <div class="spine-text">
        <div class="spine-titles">
          <span class="book-title">Crossing the Quiet River</span>
          <span class="book-subtitle">Simple Practices for Daily Calm</span>
        </div>
        <span class="spine-author">Author Name</span>
      </div>
    </section>

    <section class="panel panel-front">
      <svg class="space-art" viewBox="0 0 340 540" preserveAspectRatio="none" role="img" aria-label="Luminous figure of light rising through a blue and white nebula among planets and stars">
        <defs>
          <radialGradient id="frontGlow" cx="0.5" cy="0.45" r="0.6">
            <stop offset="0" stop-color="var(--glow-white)"/>
            <stop offset="0.2" stop-color="var(--nebula-cyan)"/>
            <stop offset="0.5" stop-color="var(--nebula-teal)" stop-opacity="0.7"/>
            <stop offset="1" stop-color="var(--space-deep)"/>
          </radialGradient>
        </defs>
        <rect width="340" height="540" fill="var(--space-deep)"/>
        <rect width="340" height="540" fill="url(#frontGlow)"/>
      </svg>
      <header class="front-heading">
        <div class="title-rule"></div>
        <h1 class="book-title">Crossing the Quiet River</h1>
        <p class="book-subtitle">Simple Practices for Daily Calm</p>
        <p class="front-author"><span class="dot">•</span>Author Name<span class="dot">•</span></p>
      </header>
    </section>
  </main>
</body>
</html>
```